Hartwell Estates Business Cards

I would like a business card that includes myself and my partner.
Includes: Logo, office #, email, website, our names, our numbers and possibly the address. I would also like the logo to be embossed and the card to be horizontal.
There is a photo of our yard signs to give you an idea of the colors of our business.

Target Market(s)

Everyone in real estate market.
We are in a rural area. Our clientele are from all socioeconomic backgrounds.

Industry/Entity Type

Real Estate Agent

Contact Information for Business Card

Company Name: Hartwell Estates
Our Names, Titles & Cell #'s : Dana Pembrook-Broker (555).317.6624, Marla Pembrook-Realtor (555).609.1385
Office #: (555).240.3918
Website: hartwellestates-demo.com
Joint Email: pembrook@hartwellestates-demo.com
Office Address: 418B W. Calloway Ave.
Larkmoor, ST. 70913

Font styles to use
Serif

Requirements
Must have
• HORIZONTAL, Logo, Myself and my partners names, Our cell #'s, our office #, our website, our email address
Nice to have
• Embossed logo, office address, our titles.

```html
<!DOCTYPE html>
<html lang="en">
<head>
<meta charset="utf-8">
<title>Hartwell Estates Business Cards</title>
<link rel="stylesheet" href="https://fonts.googleapis.com/css2?family=PT+Sans:wght@400;700&display=swap">
<style>
  :root {
    --backdrop: #ece9e4;
    --card-white: #ffffff;
    --card-shade: #e6e6e6;
    --brand-purple: #4b2070;
    --purple-deep: #3f1860;
    --purple-light: #6a3a92;
    --text-light: #ffffff;
    --silver: #d9d9de;
  }
  * { margin: 0; padding: 0; box-sizing: border-box; }
  html, body {
    width: 1200px;
    height: 843px;
    overflow: hidden;
    background: var(--backdrop);
    font-family: "PT Sans", sans-serif;
  }
  .card-set {
    position: absolute;
    inset: 0;
    display: flex;
    align-items: center;
    justify-content: center;
    gap: 40px;
  }
  .card {
    position: relative;
    width: 540px;
    height: 309px;
    border-radius: 2px;
    box-shadow: 0 6px 18px rgba(0,0,0,0.18);
    overflow: hidden;
  }
  /* Front */
  .card-front {
    background: linear-gradient(160deg, var(--card-white) 45%, var(--card-shade) 100%);
    display: flex;
    align-items: center;
    justify-content: center;
    gap: 18px;
  }
  .brand-dot {
    width: 58px;
    height: 58px;
    border-radius: 50%;
    background: var(--brand-purple);
    flex: none;
  }
  .brand-name {
    color: var(--brand-purple);
    font-weight: 700;
    font-size: 40px;
    letter-spacing: 1px;
  }
  /* Back */
  .card-back {
    background: linear-gradient(100deg, var(--purple-deep) 0%, var(--purple-light) 32%, var(--brand-purple) 60%, var(--purple-deep) 100%);
    color: var(--text-light);
  }
  .agent { position: absolute; line-height: 1.2; }
  .agent-name { font-size: 19px; font-weight: 700; }
  .agent-title, .agent-phone { font-size: 14px; }
  .agent-broker { left: 34px; top: 30px; }
  .agent-realtor { right: 34px; top: 98px; text-align: right; }
  .office {
    position: absolute;
    left: 34px;
    top: 148px;
    font-size: 14.5px;
    line-height: 1.35;
  }
  .contact-line { display: flex; align-items: center; gap: 7px; }
  .contact-line svg { width: 13px; height: 13px; flex: none; }
  .address { margin-bottom: 4px; }
  .brand-emboss {
    position: absolute;
    right: 30px;
    bottom: 28px;
    display: flex;
    align-items: center;
    gap: 9px;
    color: var(--silver);
    font-size: 15px;
    font-weight: 700;
  }
  .brand-emboss .brand-dot {
    width: 46px;
    height: 46px;
    background: var(--silver);
  }
</style>
</head>
<body>
<main class="card-set">
  <section class="card card-front" aria-label="Card front">
    <span class="brand-dot"></span>
    <span class="brand-name">Hartwell Estates</span>
  </section>

  <section class="card card-back" aria-label="Card back">
    <div class="agent agent-broker">
      <div class="agent-name">Dana Pembrook</div>
      <div class="agent-title">Broker</div>
      <div class="agent-phone">(555).317.6624</div>
    </div>

    <div class="agent agent-realtor">
      <div class="agent-name">Marla Pembrook</div>
      <div class="agent-title">Realtor</div>
      <div class="agent-phone">(555).609.1385</div>
    </div>

    <div class="office">
      <div class="address">418B W. Calloway Ave.<br>Larkmoor, ST. 70913</div>
      <div class="contact-line">
        <svg viewBox="0 0 16 16" aria-hidden="true"><path fill="currentColor" d="M3.6 1.2l2.3 2.6-1.2 1.8c.8 1.9 2.4 3.6 4.4 4.5l1.8-1.2 2.6 2.3-1.4 2.4C7.2 13.2 2.8 8.8 1.2 3.1z"/></svg>
        (555).240.3918
      </div>
      <div class="contact-line">
        <svg viewBox="0 0 16 16" aria-hidden="true"><rect x="1" y="3" width="14" height="10" fill="currentColor"/><path d="M1.5 3.5L8 9l6.5-5.5" stroke="#4b2070" stroke-width="1.3" fill="none"/></svg>
        pembrook@hartwellestates-demo.com
      </div>
      <div class="contact-line">
        <svg viewBox="0 0 16 16" aria-hidden="true"><circle cx="8" cy="8" r="7" fill="currentColor"/><path d="M1 8h14M8 1c-3 3.5-3 10.5 0 14M8 1c3 3.5 3 10.5 0 14" stroke="#4b2070" stroke-width="1" fill="none"/></svg>
        hartwellestates-demo.com
      </div>
    </div>

    <div class="brand-emboss">
      <span class="brand-dot"></span>
      <span>Hartwell Estates</span>
    </div>
  </section>
</main>
</body>
</html>
```